Business Card - connecting 2 souls and beggining the journey of self discovery

Logo on the front
with tag line

On the back list of services and contact details

Seminars
workshops
Coaching
podcasts

Darren Whitlow
Health & Wellbeing Life Coach
0491 372 615
darren@brightcoreliving.example
brightcoreliving.example

Industry/Entity Type

Life Coaching

Contact Information for Business Card

I like the use of colour from the logo to be used. I'm not a fan of white.

Requirements
Must have
• My tagline: Your path to balance begins within
Nice to have
• Use of colour that is in the mind body soul logo

```html
<!DOCTYPE html>
<html lang="en">
<head>
<meta charset="utf-8">
<title>Brightcore Living – Business Card</title>
<link rel="stylesheet" href="https://fonts.googleapis.com/css2?family=Montserrat:wght@500&family=Open+Sans:wght@400;600&display=swap">
<style>
  :root {
    --canvas-bg: #e9e6e1;
    --card-black: #050505;
    --card-white: #fbfbfb;
    --brand-grey: #7a7a7a;
    --brand-grey-light: #9a9a9a;
    --accent-green: #4cb86a;
    --text-dark: #2b2b2b;
    --mark-colour: #f08a5d;
    --faint-circle: #f1ecf4;
  }
  * { box-sizing: border-box; margin: 0; padding: 0; }
  html, body {
    width: 1200px; height: 900px; overflow: hidden;
    background: var(--canvas-bg);
  }
  .canvas {
    position: relative; width: 1200px; height: 900px;
    display: flex; align-items: center; justify-content: center; gap: 50px;
  }
  .card {
    position: relative; width: 520px; height: 318px;
    box-shadow: 0 6px 18px rgba(0,0,0,0.18);
    overflow: hidden;
  }
  /* Front */
  .card-front {
    background: var(--card-black);
    display: flex; flex-direction: column; align-items: center; justify-content: center;
  }
  .front-mark {
    width: 98px; height: 98px; border-radius: 50%;
    background: var(--mark-colour);
    margin-bottom: 26px;
  }
  .front-name {
    font-family: "Montserrat", sans-serif; font-weight: 500;
    font-size: 34px; letter-spacing: -1.2px;
    color: var(--brand-grey-light);
  }
  /* Back */
  .card-back { background: var(--card-white); }
  .back-circle {
    position: absolute; right: 18px; top: 78px;
    width: 188px; height: 188px; border-radius: 50%;
    background: var(--faint-circle);
  }
  .back-content { position: relative; padding: 40px 0 0 40px; }
  .brand-name {
    font-family: "Montserrat", sans-serif; font-weight: 500;
    font-size: 30px; letter-spacing: -1.2px; color: var(--brand-grey);
    line-height: 1;
  }
  .tagline {
    font-family: "Open Sans", sans-serif; font-weight: 600;
    font-size: 12px; letter-spacing: 0.4px; text-transform: uppercase;
    color: var(--accent-green); margin-top: 12px;
  }
  .person { margin-top: 40px; }
  .person-name {
    font-family: "Open Sans", sans-serif; font-weight: 400;
    font-size: 20px; text-transform: uppercase; color: var(--accent-green);
    line-height: 1.1;
  }
  .person-role {
    font-family: "Open Sans", sans-serif; font-size: 13px; color: var(--text-dark);
  }
  .contacts { list-style: none; margin-top: 14px; }
  .contacts li {
    display: flex; align-items: center; gap: 7px;
    font-family: "Open Sans", sans-serif; font-size: 13.5px; color: var(--text-dark);
    line-height: 1.5;
  }
  .contacts svg { width: 12px; height: 12px; flex: none; }
  .services {
    list-style: none; position: absolute; left: 40px; bottom: 22px;
    display: flex; gap: 10px;
    font-family: "Open Sans", sans-serif; font-size: 12.5px;
    text-transform: uppercase; color: var(--text-dark);
  }
  .services li { display: flex; align-items: center; gap: 5px; }
  .services li::before {
    content: ""; width: 9px; height: 9px; border-radius: 50%;
    background: var(--accent-green);
  }
</style>
</head>
<body>
<main class="canvas">
  <section class="card card-front" aria-label="Card front">
    <div class="front-mark"></div>
    <h1 class="front-name">Brightcore Living</h1>
  </section>

  <section class="card card-back" aria-label="Card back">
    <div class="back-circle"></div>
    <div class="back-content">
      <h2 class="brand-name">Brightcore Living</h2>
      <p class="tagline">Your path to balance begins within</p>
      <div class="person">
        <p class="person-name">Darren Whitlow</p>
        <p class="person-role">Health &amp; Wellbeing Life Coach</p>
      </div>
      <ul class="contacts">
        <li>
          <svg viewBox="0 0 12 12" aria-hidden="true"><path fill="#4cb86a" d="M2.5 1 4.3 1 5 3.4 3.9 4.4C4.5 5.8 5.9 7.2 7.4 7.9L8.5 6.8 11 7.5 11 9.4C11 10.3 10.2 11 9.3 11 4.7 10.6 1.4 7.3 1 2.7 1 1.8 1.6 1 2.5 1Z"/></svg>
          0491 372 615
        </li>
        <li>
          <svg viewBox="0 0 12 12" aria-hidden="true"><rect x="0.5" y="2" width="11" height="8" rx="1" fill="#4cb86a"/><path d="M1 2.6 6 6.6 11 2.6" stroke="#fff" stroke-width="1" fill="none"/></svg>
          darren@brightcoreliving.example
        </li>
        <li>
          <svg viewBox="0 0 12 12" aria-hidden="true"><circle cx="6" cy="6" r="5.5" fill="#4cb86a"/><path d="M3.5 4.5 5.5 5 5 7.5 7.5 8.5M7 2.5 6.5 4 8.5 5" stroke="#fff" stroke-width="1" fill="none"/></svg>
          brightcoreliving.example
        </li>
      </ul>
    </div>
    <ul class="services">
      <li>Seminars</li>
      <li>Workshops</li>
      <li>Coaching</li>
      <li>Podcasts</li>
    </ul>
  </section>
</main>
</body>
</html>
```